Fun, Clean Business Card For Family Focused Travel Agency

I need a business card using specific colors and fonts as in the uploaded files. Ideally, I would like a large image of the logo on the back and all the contact info on the front. Maybe the stars/dots somewhere in a flowy form.

I do want it the contact information to be clear and easy to read. I don't want it to look too busy. Maybe even a bit minimalist.

I plan or ordering the ROUNDED CORNER business cards from Cardwell Press, so please consider that in your design.

Target Market(s)

Families with children, couples, groups of friends

Contact Information for Business Card

Marla Quint, Owner
Marla@TumbleTrips.example
Cell Phone Number 555-218-4603
Office Phone Number 555-647-1925
Specializing in Glimmerland destinations, Pelican Bay Fun Park, Cruises and All-Inclusive Vacations.

Nice but not required:
www.TumbleTrips.example
Facebook, Instagram, Twitter icons with username: TumbleTrips

Font styles to use
Sans Serif

Requirements
Must have
• Please try to use the colors from the logo as much as possible. I understand lighter shades/colors may be needed for some things.
Should not have
• NO SERIF FONTS. That is really the only thing I do not want at all

```html
<!DOCTYPE html>
<html lang="en">
<head>
<meta charset="utf-8">
<title>Tumble Trips – Business Card</title>
<link href="https://fonts.googleapis.com/css2?family=Work+Sans:wght@400;500;600;700&display=swap" rel="stylesheet">
<style>
  :root {
    --navy: #0f1330;
    --orange: #ee7c22;
    --teal: #1fae8e;
    --white: #ffffff;
    --paper: #f4f4f6;
    --silver: #d9dbe0;
    --backdrop: #e6e7ea;
  }
  * { box-sizing: border-box; margin: 0; padding: 0; }
  html, body { width: 1200px; height: 900px; overflow: hidden; }
  body {
    background: var(--backdrop);
    font-family: "Work Sans", sans-serif;
    position: relative;
  }
  .card {
    position: absolute;
    left: 250px;
    width: 700px;
    height: 400px;
    border-radius: 22px;
    overflow: hidden;
    box-shadow: 0 10px 30px rgba(15, 19, 48, 0.22);
  }
  .card--front { top: 40px; background: linear-gradient(160deg, var(--white) 40%, var(--paper)); }
  .card--back { top: 460px; background: var(--navy); }

  .front-waves { position: absolute; inset: 0; width: 700px; height: 400px; }

  .brand {
    position: absolute;
    left: 70px;
    top: 52px;
    display: flex;
    align-items: center;
    gap: 12px;
  }
  .brand__dot { width: 22px; height: 22px; border-radius: 50%; background: var(--navy); }
  .brand__name { font-size: 44px; font-weight: 700; color: var(--navy); letter-spacing: -0.5px; white-space: nowrap; }

  .person {
    position: absolute;
    right: 60px;
    top: 118px;
    text-align: right;
  }
  .person__name { font-size: 30px; font-weight: 500; color: var(--orange); letter-spacing: 1.5px; text-transform: uppercase; white-space: nowrap; }
  .person__role { font-size: 15px; color: var(--navy); margin-top: 2px; }

  .social {
    position: absolute;
    left: 34px;
    top: 322px;
    display: flex;
    align-items: center;
    gap: 8px;
  }
  .social__handle { font-size: 14px; color: var(--white); margin-right: 6px; white-space: nowrap; flex: none; }
  .social__icon { width: 18px; height: 18px; border-radius: 4px; background: var(--silver); flex: none; }

  .contact {
    position: absolute;
    right: 40px;
    bottom: 22px;
    list-style: none;
    text-align: right;
  }
  .contact__item {
    display: flex;
    justify-content: flex-end;
    align-items: center;
    gap: 10px;
    font-size: 14px;
    line-height: 22px;
    color: var(--white);
    letter-spacing: 0.3px;
    white-space: nowrap;
  }
  .contact__icon { width: 13px; height: 13px; flex: none; }

  .back-brand {
    position: absolute;
    left: 0; right: 0;
    top: 110px;
    display: flex;
    justify-content: center;
    align-items: center;
    gap: 18px;
  }
  .back-brand__dot { width: 40px; height: 40px; border-radius: 50%; background: var(--silver); }
  .back-brand__name { font-size: 76px; font-weight: 700; color: var(--silver); letter-spacing: -1px; white-space: nowrap; }
  .tagline {
    position: absolute;
    left: 60px; right: 60px;
    top: 260px;
    text-align: center;
    font-size: 18px;
    line-height: 28px;
    color: var(--silver);
  }
</style>
</head>
<body>

<section class="card card--front" aria-label="Business card front">
  <svg class="front-waves" viewBox="0 0 700 400" aria-hidden="true">
    <path d="M0,120 C40,215 150,272 330,274 C480,276 600,258 700,212 L700,400 L0,400 Z" fill="#1fae8e"/>
    <path d="M0,150 C60,235 170,282 340,284 C490,286 610,268 700,228 L700,400 L0,400 Z" fill="#0f1330"/>
    <path d="M50,140 C110,215 220,258 380,258 C520,258 620,242 692,205" fill="none" stroke="#ee7c22" stroke-width="8" stroke-linecap="round"/>
  </svg>

  <div class="brand">
    <span class="brand__dot"></span>
    <span class="brand__name">Tumble Trips</span>
  </div>

  <div class="person">
    <p class="person__name">Marla Quint</p>
    <p class="person__role">Owner</p>
  </div>

  <div class="social">
    <span class="social__handle">TumbleTrips</span>
    <span class="social__icon"></span>
    <span class="social__icon"></span>
    <span class="social__icon"></span>
  </div>

  <ul class="contact">
    <li class="contact__item">555-218-4603
      <svg class="contact__icon" viewBox="0 0 12 12"><rect x="3" y="0.5" width="6" height="11" rx="1.2" fill="none" stroke="#ee7c22" stroke-width="1.3"/><circle cx="6" cy="9.5" r="0.8" fill="#ee7c22"/></svg>
    </li>
    <li class="contact__item">555-647-1925
      <svg class="contact__icon" viewBox="0 0 12 12"><path d="M2.5,1 L4.5,1 L5.3,3.6 L4,4.6 C4.6,6 5.9,7.4 7.4,8 L8.4,6.7 L11,7.5 L11,9.5 C11,10.4 10.3,11 9.5,11 C5,10.6 1.4,7 1,2.5 C1,1.7 1.6,1 2.5,1 Z" fill="#ee7c22"/></svg>
    </li>
    <li class="contact__item">Marla@TumbleTrips.example
      <svg class="contact__icon" viewBox="0 0 12 12"><rect x="0.7" y="2.2" width="10.6" height="7.6" rx="1" fill="none" stroke="#ee7c22" stroke-width="1.3"/><path d="M1,2.8 L6,6.6 L11,2.8" fill="none" stroke="#ee7c22" stroke-width="1.3"/></svg>
    </li>
    <li class="contact__item">www.TumbleTrips.example
      <svg class="contact__icon" viewBox="0 0 12 12"><circle cx="6" cy="6" r="5.2" fill="none" stroke="#ee7c22" stroke-width="1.2"/><ellipse cx="6" cy="6" rx="2.2" ry="5.2" fill="none" stroke="#ee7c22" stroke-width="1"/><path d="M1,6 H11" stroke="#ee7c22" stroke-width="1"/></svg>
    </li>
  </ul>
</section>

<section class="card card--back" aria-label="Business card back">
  <div class="back-brand">
    <span class="back-brand__dot"></span>
    <span class="back-brand__name">Tumble Trips</span>
  </div>
  <p class="tagline">Specializing in Glimmerland destinations, Pelican Bay Fun Park,<br>Cruises and All-Inclusive Vacations.</p>
</section>

</body>
</html>
```